Brookmere Osteopathy flyer

I want a clean clear DL flyer (but also want an A4 poster) promoting a new Osteopathic business in a semi rural area in Tasmania (Australia).
It can have pictures like the examples attached to show people what Osteopathy is (its like Chiropractic and physiotherapy).
I am the sole practioner and am male, so any pictures would be best to be a white male if possible.
I've attached some wording, you can use all, or none of it
I don't have a phone number for the business yet
info@brookmereosteopathy.example
www.brookmereosteopathy.example
Target Market(s)
Australians, from tradies, professionals, babies to retired people
Industry/Entity Type
Health
Look and feel

```html
<!DOCTYPE html>
<html lang="en">
<head>
<meta charset="utf-8">
<title>Brookmere Osteopathy – Poster and DL Flyer</title>
<link rel="stylesheet" href="https://fonts.googleapis.com/css2?family=Outfit:wght@300;400;500;700;800&family=Space+Grotesk:wght@400;500;700&display=swap">
<style>
  :root{
    --board:#8eaad6;
    --blue:#1195d6;
    --navy:#123f8f;
    --deep:#1a4fa6;
    --sky:#8fdcfb;
    --orange:#f18a32;
    --white:#ffffff;
    --ink:#1c2230;
    --grey:#4a5160;
  }
  *{margin:0;padding:0;box-sizing:border-box}
  html,body{width:1200px;height:997px;overflow:hidden;background:var(--board)}
  .board{position:relative;width:1200px;height:997px;background:var(--board);font-family:"Outfit",sans-serif}
  .board-label{position:absolute;top:47px;font:500 16px "Outfit",sans-serif;letter-spacing:1.5px;color:var(--white);transform:translateX(-50%)}
  .label-poster{left:383px}
  .label-flyer{left:916px}

  /* ---------- Poster ---------- */
  .poster{position:absolute;left:87px;top:81px;width:592px;height:836px;overflow:hidden;
    background:linear-gradient(180deg,#3a8fcf 0%,#1c5fb0 55%,#163f8c 100%);
    box-shadow:0 18px 26px rgba(30,50,90,.35);font-family:"Space Grotesk",sans-serif;color:var(--white)}
  .poster-photo{position:absolute;left:0;top:0;width:592px;height:520px;
    background:linear-gradient(180deg,rgba(214,205,190,1) 0%,rgba(190,196,198,1) 40%,rgba(120,170,190,.9) 70%,rgba(60,140,200,0) 100%)}
  .poster-warm{position:absolute;inset:0;
    background:linear-gradient(135deg,rgba(240,190,60,.55) 0%,rgba(240,190,60,0) 30%),
               linear-gradient(270deg,rgba(232,128,50,.65) 0%,rgba(232,128,50,0) 45%)}
  .poster-badge{position:absolute;left:395px;top:232px;width:160px;height:160px;border-radius:50%;
    background:var(--white);border:4px solid var(--blue);display:flex;align-items:center;justify-content:center;text-align:center;
    font:700 17px/1.15 "Space Grotesk",sans-serif;color:var(--blue);padding:18px}
  .poster-word{position:absolute;font-weight:700;line-height:1;white-space:nowrap}
  .word-common{left:34px;top:358px;font-size:70px;letter-spacing:-2px}
  .word-reasons{left:72px;top:406px;font-size:72px;letter-spacing:-2.5px;color:var(--sky)}
  .poster-tag{position:absolute;left:112px;top:472px;width:210px;height:52px;background:var(--orange);transform:rotate(-3deg);
    display:flex;align-items:center;justify-content:center;font:700 30px "Space Grotesk",sans-serif;color:var(--ink);z-index:1}
  .word-osteopath{left:72px;top:507px;font-size:58px;letter-spacing:-2px;z-index:2}
  .poster-list{position:absolute;left:35px;top:580px;width:390px;font-size:14.6px;line-height:20.6px}
  .poster-rule{position:absolute;left:36px;top:724px}
  .poster-contact{position:absolute;left:36px;top:749px;list-style:none;font-size:13.8px;line-height:18px}
  .poster-contact li{display:flex;align-items:center;gap:8px}
  .poster-note{position:absolute;left:328px;top:686px;width:228px;height:113px;background:var(--sky);color:var(--ink);
    padding:10px 12px;font-size:12.4px;line-height:15px}

  /* ---------- DL Flyer ---------- */
  .flyer{position:absolute;left:719px;top:81px;width:394px;height:836px;overflow:hidden;background:var(--white);
    box-shadow:0 18px 26px rgba(30,50,90,.35);color:var(--ink)}
  .flyer svg.shapes{position:absolute;left:0;top:0}
  .flyer-art{position:absolute}
  .art-spine-top{left:315px;top:5px;width:78px;height:171px;border-radius:40px;background:linear-gradient(180deg,#3a5fd0,#2a3f9e)}
  .art-pelvis{left:1px;top:210px;width:109px;height:150px;border-radius:50px 50px 30px 30px;background:linear-gradient(180deg,#f4ebe6,#e8cfc8)}
  .art-figure{left:12px;top:627px;width:172px;height:206px;border-radius:80px 80px 10px 10px;background:radial-gradient(circle at 60% 50%,#e0452a 0%,#1d5fe0 35%,#0b2f9a 100%)}
  .art-spine-bottom{left:240px;top:632px;width:150px;height:44px;border-radius:22px;background:linear-gradient(90deg,#5b6a88,#2c3550);transform:rotate(18deg)}
  .flyer-common{position:absolute;left:61px;top:30px;font:800 51px/1 "Outfit",sans-serif;color:var(--white);letter-spacing:-1px}
  .flyer-reasons{position:absolute;left:131px;top:72px;width:207px;height:64px;background:var(--orange);border-radius:6px;transform:rotate(-2deg);
    display:flex;align-items:center;justify-content:center;font:800 46px "Outfit",sans-serif;color:var(--white);letter-spacing:-1px}
  .flyer-sub{position:absolute;left:0;width:394px;text-align:center;color:var(--white)}
  .flyer-sub.visit{top:148px;font:500 28px "Outfit",sans-serif;letter-spacing:-.5px}
  .flyer-sub.osteo{top:179px;font:800 43px "Outfit",sans-serif;letter-spacing:-.5px}
  .flyer-badge{position:absolute;left:135px;top:242px;width:132px;height:132px;border-radius:50%;background:var(--white);
    border:3px solid var(--blue);box-shadow:0 6px 14px rgba(0,0,0,.18);display:flex;align-items:center;justify-content:center;text-align:center;
    font:700 14px/1.15 "Outfit",sans-serif;color:var(--blue);padding:14px}
  .flyer-list{position:absolute;top:397px;list-style:none;font:400 14px/1.15 "Outfit",sans-serif}
  .flyer-list li{position:relative;padding-left:22px;margin-bottom:6.5px}
  .flyer-list li::before{content:"";position:absolute;left:2px;top:3px;width:10px;height:10px;border-radius:50%;background:var(--blue)}
  .flyer-list.right li::before{background:var(--orange)}
  .flyer-list.left{left:26px}
  .flyer-list.right{left:218px}
  .flyer-divider{position:absolute;left:203px;top:393px;width:1px;height:137px;background:var(--grey)}
  .flyer-text{position:absolute;left:30px;top:550px;width:334px;text-align:center;font:300 14px/17px "Outfit",sans-serif;color:var(--grey)}
  .flyer-contact{position:absolute;left:226px;top:704px;width:160px;list-style:none;font:400 13px/1.05 "Outfit",sans-serif;color:var(--white)}
  .flyer-contact li{display:flex;gap:5px;margin-bottom:7px}
  .flyer-contact svg{flex:none;margin-top:1px}
</style>
</head>
<body>
<div class="board">
  <div class="board-label label-poster">POSTER DESIGN</div>
  <div class="board-label label-flyer">DL FLYER DESIGN</div>

  <section class="poster">
    <div class="poster-photo" role="img" aria-label="Photo of an osteopath in blue scrubs assessing a seated patient's back in a clinic room"></div>
    <div class="poster-warm"></div>
    <div class="poster-badge">Brookmere Osteopathy</div>

    <h1 class="poster-word word-common">common</h1>
    <div class="poster-word word-reasons">reasons</div>
    <div class="poster-tag">people visit</div>
    <div class="poster-word word-osteopath">an osteopath</div>

    <p class="poster-list">Back / neck pain &nbsp;|&nbsp; Headaches / migraines &nbsp;|&nbsp; Joint and muscle pain &nbsp;|&nbsp; Pregnancy-related discomfort &nbsp;|&nbsp; Disc related issues &nbsp;|&nbsp; Sciatica &nbsp;|&nbsp; Plantar fasciitis &nbsp;|&nbsp;Tendonitis / Bursitis &nbsp;|&nbsp; Adhesive capsulitis (frozen shoulder) &nbsp;|&nbsp; Tennis / Golfers elbow</p>

    <svg class="poster-rule" width="232" height="12" viewBox="0 0 232 12"><path d="M1 6 C40 2 80 2 118 3 L112 9 C150 6 190 5 230 4" fill="none" stroke="var(--orange)" stroke-width="2" stroke-linecap="round"/></svg>

    <ul class="poster-contact">
      <li><svg width="9" height="9" viewBox="0 0 10 10"><path d="M2 1 L4 1 L5 3 L4 4 C5 6 6 7 7 7 L8 6 L10 7 L10 9 C5 10 0 5 1 1Z" fill="var(--orange)"/></svg>42 Wattle Creek Road, Brookmere</li>
      <li><svg width="9" height="9" viewBox="0 0 10 10"><path d="M1 1 L9 5 L5 6 L3 9Z" fill="var(--orange)"/></svg>www.brookmereosteopathy.example</li>
      <li><svg width="9" height="9" viewBox="0 0 10 10"><rect x="0" y="2" width="10" height="7" fill="var(--orange)"/><path d="M0 2 L5 6 L10 2" fill="none" stroke="#163f8c" stroke-width="1"/></svg>info@brookmereosteopathy.example</li>
    </ul>

    <div class="poster-note">Osteopaths use a combination of joint manipulation, targeted deep tissue massage and stretching to improve function, relieve pain and support the body's ability to heal itself.</div>
  </section>

  <section class="flyer">
    <svg class="shapes" width="394" height="836" viewBox="0 0 394 836">
      <path d="M23 0 H369 V270 C369 360 310 372 230 375 L110 378 C50 378 23 330 23 250 Z" fill="var(--blue)"/>
      <circle cx="378" cy="862" r="215" fill="var(--orange)"/>
    </svg>
    <div class="flyer-art art-spine-top" role="img" aria-label="Illustration of blue vertebrae"></div>
    <div class="flyer-art art-pelvis" role="img" aria-label="Illustration of a pelvis and lower spine"></div>
    <div class="flyer-art art-figure" role="img" aria-label="Illustration of a seated figure holding a painful knee"></div>
    <div class="flyer-art art-spine-bottom" role="img" aria-label="Illustration of a spine"></div>

    <div class="flyer-common">Common</div>
    <div class="flyer-reasons">Reasons</div>
    <div class="flyer-sub visit">People Visit An</div>
    <div class="flyer-sub osteo">Osteopath</div>
    <div class="flyer-badge">Brookmere Osteopathy</div>

    <ul class="flyer-list left">
      <li>Back / neck pain</li>
      <li>Headaches / migraines</li>
      <li>Joint and muscle pain</li>
      <li>Pregnancy-related<br>discomfort</li>
      <li>Disc related issues</li>
    </ul>
    <div class="flyer-divider"></div>
    <ul class="flyer-list right">
      <li>Sciatica</li>
      <li>Plantar fasciitis</li>
      <li>Tendonitis / Bursitis</li>
      <li>Adhesive capsulitis<br>(frozen shoulder)</li>
      <li>Tennis / Golfers elbow</li>
    </ul>

    <p class="flyer-text">Osteopaths use a combination of joint manipulation, targeted deep tissue massage and stretching to improve function, relieve pain and support the body's ability to heal itself.</p>

    <ul class="flyer-contact">
      <li><svg width="9" height="12" viewBox="0 0 10 13"><path d="M5 0 C8 0 10 2 10 5 C10 8 5 13 5 13 C5 13 0 8 0 5 C0 2 2 0 5 0Z" fill="var(--white)"/><circle cx="5" cy="5" r="2" fill="var(--orange)"/></svg><span>Wattle Creek Road,<br>Brookmere</span></li>
      <li><svg width="10" height="10" viewBox="0 0 10 10"><path d="M2 1 L4 1 L5 3 L4 4 C5 6 6 7 7 7 L8 6 L10 7 L10 9 C5 10 0 5 1 1Z" fill="var(--white)"/></svg><span>0400 000 000</span></li>
      <li><svg width="10" height="10" viewBox="0 0 10 10"><path d="M1 1 L9 5 L5 6 L3 9Z" fill="var(--white)"/></svg><span>www.brookmere<br>osteopathy.example</span></li>
      <li><svg width="10" height="10" viewBox="0 0 10 10"><rect x="0" y="2" width="10" height="7" fill="var(--white)"/><path d="M0 2 L5 6 L10 2" fill="none" stroke="var(--orange)" stroke-width="1"/></svg><span>info@brookmere<br>osteopathy.example</span></li>
    </ul>
  </section>
</div>
</body>
</html>
```